Norvane Stationery Design Project

We need stationary design that goes with the attached logo. We have logo in two different versions. One in Red/Black and the other in Blue/Green. Red/Black is going to be our primary color and we are planning to use Blue/Green occasionally as necessary.

So we need stationary design in both color combinations. Maybe you can work with Red/Black first and once we decide on the design, then you can show the Blue/Green variation.

Please see the attached png and psd files for logo.

Target Market(s)

IT departments of Medium size Enterprises.

Industry/Entity Type

Work

Requirements
Must have
• -Letter head
-Cover page design for white papers and articles that are going to publish
-Business Card
-Envelope design
Nice to have
• - High level design template that we can follow for our internal web applications

```html
<!DOCTYPE html>
<html lang="en">
<head>
<meta charset="utf-8">
<title>Norvane Software – Business Card</title>
<link rel="stylesheet" href="https://fonts.googleapis.com/css2?family=Lato:wght@400;700;900&display=swap">
<style>
  :root {
    --backdrop: #2b2b2b;
    --card-white: #ffffff;
    --card-shade: #ececec;
    --brand-red: #c8141b;
    --brand-red-dark: #9e0d12;
    --ink: #1c1c1c;
    --on-red: #ffffff;
    --on-red-soft: rgba(255,255,255,0.85);
  }
  * { margin: 0; padding: 0; box-sizing: border-box; }
  html, body {
    width: 1200px; height: 997px; overflow: hidden;
    background: var(--backdrop);
    font-family: "Lato", Arial, sans-serif;
  }
  .canvas { position: relative; width: 1200px; height: 997px; }

  .card {
    position: absolute;
    width: 640px; height: 366px;
    background: linear-gradient(180deg, var(--card-white) 0%, var(--card-shade) 100%);
    box-shadow: 0 14px 34px rgba(0,0,0,0.55);
    overflow: hidden;
  }
  .card--front { left: 110px; top: 80px; }
  .card--back  { left: 450px; top: 520px; }

  .wordmark {
    position: absolute;
    display: flex; align-items: center; gap: 16px;
    color: var(--ink);
    font-weight: 900;
    letter-spacing: 0.14em;
    text-transform: uppercase;
    white-space: nowrap;
  }
  .wordmark__square { background: var(--brand-red); flex: none; }
  .card--front .wordmark { left: 50%; top: 50%; transform: translate(-50%, -50%); font-size: 34px; }
  .card--front .wordmark__square { width: 46px; height: 46px; }
  .card--back .wordmark { left: 50%; top: 58px; transform: translateX(-50%); font-size: 28px; }
  .card--back .wordmark__square { width: 38px; height: 38px; }

  .band { position: absolute; left: 0; top: 0; width: 640px; height: 366px; }

  .holder-name {
    position: absolute; left: 36px; top: 140px;
    font-size: 20px; font-weight: 900; letter-spacing: 0.06em;
    color: var(--ink);
  }

  .contact-list {
    position: absolute; left: 36px; top: 214px;
    list-style: none;
  }
  .contact-list li {
    display: flex; align-items: center; gap: 14px;
    height: 36px;
    font-size: 19px; font-weight: 700;
    color: var(--on-red);
  }
  .contact-list svg { width: 20px; height: 20px; flex: none; }

  .company-info {
    position: absolute; right: 32px; top: 206px;
    text-align: left; color: var(--on-red);
  }
  .company-info__web { font-size: 18px; font-weight: 900; letter-spacing: 0.02em; }
  .company-info__rule { height: 2px; background: var(--on-red-soft); margin: 9px 0 10px; }
  .company-info__address { font-size: 14px; font-weight: 700; color: var(--on-red-soft); }
</style>
</head>
<body>
<main class="canvas">

  <section class="card card--front" aria-label="Business card front">
    <div class="wordmark"><span class="wordmark__square"></span><span>Norvane Software</span></div>
  </section>

  <section class="card card--back" aria-label="Business card back">
    <svg class="band" viewBox="0 0 640 366" aria-hidden="true">
      <defs>
        <linearGradient id="redBand" x1="0" y1="0" x2="1" y2="1">
          <stop offset="0" stop-color="#d0171e"/>
          <stop offset="1" stop-color="#9e0d12"/>
        </linearGradient>
      </defs>
      <path d="M0 182 H72 L86 198 L100 182 H640 V366 H0 Z" fill="url(#redBand)"/>
    </svg>

    <div class="wordmark"><span class="wordmark__square"></span><span>Norvane Software</span></div>

    <p class="holder-name">YOUR NAME</p>

    <ul class="contact-list">
      <li>
        <svg viewBox="0 0 20 20" aria-hidden="true"><rect x="5" y="1.5" width="10" height="17" rx="2" fill="none" stroke="#fff" stroke-width="1.8"/><circle cx="10" cy="15.5" r="1" fill="#fff"/></svg>
        (555) 014-2210
      </li>
      <li>
        <svg viewBox="0 0 20 20" aria-hidden="true"><path d="M2 7 Q10 1 18 7 L15 9 L13 7 H7 L5 9 Z" fill="#fff"/><rect x="4" y="10" width="12" height="8" rx="1.5" fill="#fff"/></svg>
        (555) 017-3380
      </li>
      <li>
        <svg viewBox="0 0 20 20" aria-hidden="true"><rect x="1.5" y="4" width="17" height="12" fill="none" stroke="#fff" stroke-width="1.8"/><path d="M1.5 4 L10 11 L18.5 4" fill="none" stroke="#fff" stroke-width="1.8"/></svg>
        info@norvanesoftware.com
      </li>
    </ul>

    <div class="company-info">
      <p class="company-info__web">www.norvanesoftware.com</p>
      <div class="company-info__rule"></div>
      <p class="company-info__address">P.O. Box 27, Larkfield AL, 36990</p>
    </div>
  </section>

</main>
</body>
</html>
```